2021 Summer Ads Hollis Bay Custom Homes

We need a re-design of our summer ad run for our customer, Hollis Bay Custom Homes. They are custom home builders in the mostly rural parts of West Virginia, USA. They are known for their "Forever Home" tagline. We'd like two designed ads with the main difference being just the custom home that's featured. These designs should be for a Zintrola banner like 300 x 250 and square ad like 250 x 250. For inspiration please visit the Hollis Bay Custom Homes website at www dot hollisbaycustomhomes dot com

Target Market(s)

consumers / new home shoppers

Industry/Entity Type

Consumer

Requirements
Must have
• HBCH logo
Price Lock Available!
Custom home pic
Learn more >
small CFRM logo mark

```html
<!DOCTYPE html>
<html lang="en">
<head>
<meta charset="utf-8">
<title>Hollis Bay Custom Homes – Summer Display Ads</title>
<link href="https://fonts.googleapis.com/css2?family=Montserrat:wght@400;500;600;700;900&display=swap" rel="stylesheet">
<style>
  :root {
    --board-light: #c4c4c4;
    --board-dark: #a9a9a9;
    --brand-red: #cc0000;
    --brand-red-dark: #a80000;
    --ink: #1f1f2b;
    --ink-soft: #3a3a3a;
    --paper: #ffffff;
    --paper-shade: #eeeeee;
    --label: #555555;
    --badge: #2b3f9c;
  }
  * { margin: 0; padding: 0; box-sizing: border-box; }
  html, body { width: 1200px; height: 1200px; overflow: hidden; }
  body {
    background: radial-gradient(circle at 50% 45%, var(--board-light), var(--board-dark));
    font-family: "Montserrat", Arial, sans-serif;
    position: relative;
  }
  .ad {
    position: absolute;
    left: 339px;
    width: 522px;
    filter: drop-shadow(10px 12px 8px rgba(0,0,0,0.45));
  }
  .ad--square { top: 63px; height: 522px; }
  .ad--banner { top: 670px; height: 435px; }
  .ad svg { display: block; width: 100%; height: 100%; }
  .size-label {
    position: absolute;
    left: 0; width: 1200px;
    text-align: center;
    font-weight: 600;
    font-size: 35px;
    color: var(--label);
    letter-spacing: 1px;
  }
  .size-label--square { top: 610px; }
  .size-label--banner { top: 1130px; }

  .brand-name { font-family: "Montserrat", Arial, sans-serif; font-weight: 800; fill: var(--brand-red); }
  .tag-forever { font-family: "Montserrat", Arial, sans-serif; font-weight: 400; fill: var(--ink-soft); }
  .tag-home { font-family: "Montserrat", Arial, sans-serif; font-weight: 900; fill: var(--brand-red); }
  .tag-lock { font-family: "Montserrat", Arial, sans-serif; font-weight: 500; fill: var(--ink-soft); }
  .tag-lock-strong { font-weight: 700; fill: var(--ink); }
  .cta-text { font-family: "Montserrat", Arial, sans-serif; font-weight: 500; fill: var(--paper); }
  .site-url { font-family: "Montserrat", Arial, sans-serif; font-weight: 500; fill: var(--paper); }
  .site-url-strong { font-weight: 700; }
</style>
</head>
<body>

<!-- Square ad 250 x 250 -->
<div class="ad ad--square">
  <svg viewBox="0 0 840 840" xmlns="http://www.w3.org/2000/svg">
    <defs>
      <linearGradient id="sq-feature" x1="0" y1="0" x2="0" y2="1">
        <stop offset="0" stop-color="#3f8ccf"/>
        <stop offset="0.35" stop-color="#dfe3e1"/>
        <stop offset="0.7" stop-color="#8a8c8c"/>
        <stop offset="1" stop-color="#2f6b23"/>
      </linearGradient>
      <linearGradient id="sq-second" x1="0" y1="0" x2="0" y2="1">
        <stop offset="0" stop-color="#3f6b2d"/>
        <stop offset="0.4" stop-color="#a52a1c"/>
        <stop offset="1" stop-color="#8a8078"/>
      </linearGradient>
      <linearGradient id="sq-cta" x1="0" y1="0" x2="0" y2="1">
        <stop offset="0" stop-color="#e21b1b"/>
        <stop offset="1" stop-color="var(--brand-red-dark)"/>
      </linearGradient>
      <linearGradient id="sq-paper" x1="0" y1="0" x2="1" y2="1">
        <stop offset="0" stop-color="var(--paper-shade)"/>
        <stop offset="0.5" stop-color="var(--paper)"/>
      </linearGradient>
    </defs>
    <rect width="840" height="840" fill="url(#sq-paper)"/>
    <polygon points="489,0 524,0 378,350 342,380" fill="var(--brand-red)"/>
    <polygon points="524,0 840,0 840,693 470,693 320,485 378,350" fill="url(#sq-feature)" role="img" aria-label="Photo of a white board-and-batten custom garage home with dark roof and stone base"/>
    <polygon points="0,505 305,505 445,690 390,840 0,840" fill="url(#sq-second)" role="img" aria-label="Photo of a red board-and-batten barn-style custom home"/>
    <polygon points="470,715 840,715 840,840 392,840" fill="var(--brand-red)"/>

    <rect x="40" y="112" width="22" height="22" fill="var(--brand-red)"/>
    <text class="brand-name" x="76" y="134" font-size="44">HOLLIS BAY</text>
    <text class="brand-name" x="76" y="172" font-size="22" letter-spacing="5">CUSTOM HOMES</text>

    <text class="tag-forever" x="34" y="278" font-size="58">Forever</text>
    <text class="tag-home" x="30" y="360" font-size="96">HOME</text>
    <text class="tag-lock" x="34" y="398" font-size="28">Price Lock <tspan class="tag-lock-strong">Available!</tspan></text>

    <rect x="30" y="424" width="187" height="42" rx="5" fill="url(#sq-cta)"/>
    <text class="cta-text" x="45" y="453" font-size="24">Learn more</text>
    <circle cx="196" cy="445" r="7" fill="var(--ink)"/>
    <path d="M194 441 L198 445 L194 449" stroke="var(--paper)" stroke-width="2" fill="none"/>

    <rect x="239" y="421" width="65" height="47" rx="4" fill="var(--badge)"/>

    <text class="site-url" x="627" y="786" font-size="26" text-anchor="middle">www.<tspan class="site-url-strong">brightfieldbuilders</tspan>.com</text>
  </svg>
</div>
<div class="size-label size-label--square">250 X 250</div>

<!-- Banner ad 300 x 250 -->
<div class="ad ad--banner">
  <svg viewBox="0 0 840 700" xmlns="http://www.w3.org/2000/svg">
    <defs>
      <linearGradient id="bn-feature" x1="0" y1="0" x2="0" y2="1">
        <stop offset="0" stop-color="#3f8ccf"/>
        <stop offset="0.35" stop-color="#dfe3e1"/>
        <stop offset="0.7" stop-color="#8a8c8c"/>
        <stop offset="1" stop-color="#2f6b23"/>
      </linearGradient>
      <linearGradient id="bn-second" x1="0" y1="0" x2="0" y2="1">
        <stop offset="0" stop-color="#3f6b2d"/>
        <stop offset="0.4" stop-color="#a52a1c"/>
        <stop offset="1" stop-color="#8a8078"/>
      </linearGradient>
      <linearGradient id="bn-cta" x1="0" y1="0" x2="0" y2="1">
        <stop offset="0" stop-color="#e21b1b"/>
        <stop offset="1" stop-color="var(--brand-red-dark)"/>
      </linearGradient>
      <linearGradient id="bn-paper" x1="0" y1="0" x2="1" y2="1">
        <stop offset="0" stop-color="var(--paper-shade)"/>
        <stop offset="0.5" stop-color="var(--paper)"/>
      </linearGradient>
    </defs>
    <rect width="840" height="700" fill="url(#bn-paper)"/>
    <polygon points="444,0 477,0 355,290 324,312" fill="var(--brand-red)"/>
    <polygon points="477,0 840,0 840,577 455,577 305,400 355,290" fill="url(#bn-feature)" role="img" aria-label="Photo of a white custom garage home with cupola, dark roof and stone base"/>
    <polygon points="0,421 300,421 440,585 392,700 0,700" fill="url(#bn-second)" role="img" aria-label="Photo of a red board-and-batten barn-style custom home"/>
    <polygon points="455,596 840,596 840,700 392,700" fill="var(--brand-red)"/>

    <rect x="42" y="98" width="20" height="20" fill="var(--brand-red)"/>
    <text class="brand-name" x="74" y="118" font-size="40">HOLLIS BAY</text>
    <text class="brand-name" x="74" y="152" font-size="20" letter-spacing="5">CUSTOM HOMES</text>

    <text class="tag-forever" x="36" y="236" font-size="54">Forever</text>
    <text class="tag-home" x="32" y="306" font-size="84">HOME</text>
    <text class="tag-lock" x="36" y="339" font-size="26">Price Lock <tspan class="tag-lock-strong">Available!</tspan></text>

    <rect x="32" y="362" width="164" height="37" rx="5" fill="url(#bn-cta)"/>
    <text class="cta-text" x="45" y="388" font-size="21">Learn more</text>
    <circle cx="178" cy="380" r="6" fill="var(--ink)"/>
    <path d="M176 377 L180 380 L176 383" stroke="var(--paper)" stroke-width="2" fill="none"/>

    <rect x="222" y="361" width="60" height="42" rx="4" fill="var(--badge)"/>

    <text class="site-url" x="632" y="658" font-size="24" text-anchor="middle">www.<tspan class="site-url-strong">brightfieldbuilders</tspan>.com</text>
  </svg>
</div>
<div class="size-label size-label--banner">300 X 250</div>

</body>
</html>
```